32 x 24 Swinging Real Estate Yard Sign

We are looking to design a new sign for our business to focus on the remodeling of homes to sell. We are looking to have a yard sign that gets peoples attention and is informational. The headline will be "The Secret to Top Dollar? Remodel First.". We remodel homes for sellers with no up front cost, as they simply pay at closing. This link has more info, https://bramblecresthomes.com/Remodel
The message we want to convey to those seeing the sign is we are a one stop shop, who can renovate your home and sell it for no stress. We are licensed real estate agents and licensed contractors.
Both of these license numbers and info need to be on the design:
CADRE #02794613
Contractors License #1178524
Email: info@bramblecresthomes.com
Phone: (408)614-2907
I'll attach a sample sign we have for our agents normally as well as all brand art work.
• Pantone Colors
o #172A41
Dark blue
o #4381B1
Medium blue
o #6FA6CC
Light blue
Target Market(s)
Residential Real Estate Sellers
Industry/Entity Type
Real Estate
Colors
Designer to choose colors to be used in the design.

```html
<!DOCTYPE html>
<html lang="en">
<head>
<meta charset="utf-8">
<title>Bramblecrest Homes Yard Sign</title>
<link href="https://fonts.googleapis.com/css2?family=Montserrat:wght@400;500;600;700;900&display=swap" rel="stylesheet">
<style>
  :root {
    --navy: #172A41;
    --blue: #4381B1;
    --steel: #3D6B94;
    --sky: #6FA6CC;
    --white: #FFFFFF;
    --backdrop: #E9ECEF;
  }
  * { margin: 0; padding: 0; box-sizing: border-box; }
  html, body {
    width: 1200px; height: 1200px; overflow: hidden;
    background: var(--backdrop);
    font-family: "Montserrat", sans-serif;
  }
  .yard-sign {
    position: absolute; left: 194px; top: 40px;
    width: 812px; height: 1120px;
    background: var(--white);
    box-shadow: 0 6px 24px rgba(23, 42, 65, 0.18);
  }
  .brand-band {
    position: absolute; left: 0; top: 0;
    width: 812px; height: 342px;
  }
  .brand-name {
    position: absolute; left: 0; top: 120px; width: 812px;
    display: flex; align-items: center; justify-content: center; gap: 22px;
  }
  .brand-dot {
    width: 46px; height: 46px; border-radius: 50%;
    background: var(--sky);
  }
  .brand-text {
    color: var(--white); font-weight: 600; font-size: 46px;
    letter-spacing: 3px; line-height: 1;
  }
  .agent { position: absolute; left: 70px; top: 440px; }
  .agent-first {
    color: var(--steel); font-weight: 400; font-size: 150px;
    line-height: 1; letter-spacing: -2px;
  }
  .agent-last {
    color: var(--navy); font-weight: 900; font-size: 78px;
    line-height: 1; margin-top: 4px; letter-spacing: -1px;
  }
  .agent-email {
    color: var(--blue); font-weight: 500; font-size: 34px;
    line-height: 1; margin-top: 14px;
  }
  .offer {
    position: absolute; left: 70px; top: 782px; width: 672px;
  }
  .offer-headline {
    color: var(--navy); font-weight: 700; font-size: 34px; line-height: 1.15;
  }
  .offer-headline em { font-style: normal; color: var(--blue); }
  .offer-terms {
    color: var(--steel); font-weight: 500; font-size: 21px;
    line-height: 1.2; margin-top: 10px;
  }
  .offer-link {
    color: var(--navy); font-weight: 600; font-size: 19px;
    line-height: 1.2; margin-top: 6px;
  }
  .contact { position: absolute; left: 70px; top: 968px; }
  .contact-phone {
    color: var(--blue); font-weight: 700; font-size: 61px; line-height: 1;
  }
  .contact-web {
    color: var(--navy); font-weight: 500; font-size: 32px;
    line-height: 1; margin-top: 12px;
  }
  .licenses {
    position: absolute; left: 584px; top: 966px;
    color: var(--navy); font-weight: 500; font-size: 16.5px; line-height: 1.35;
  }
  .licenses p + p { margin-top: 22px; }
</style>
</head>
<body>
  <main class="yard-sign">
    <svg class="brand-band" viewBox="0 0 812 342" aria-hidden="true">
      <polygon points="0,0 812,0 812,296 482,296 416,342 350,296 0,296" fill="var(--navy)"/>
    </svg>
    <div class="brand-name">
      <span class="brand-dot"></span>
      <span class="brand-text">BRAMBLECREST HOMES</span>
    </div>

    <section class="agent">
      <h1 class="agent-first">DANIEL</h1>
      <h2 class="agent-last">HARTLEY</h2>
      <p class="agent-email">info@bramblecresthomes.com</p>
    </section>

    <section class="offer">
      <h3 class="offer-headline">The Secret to Top Dollar?<br><em>Remodel First.</em></h3>
      <p class="offer-terms">No upfront cost. You simply pay at closing.</p>
      <p class="offer-link">bramblecresthomes.com/Remodel</p>
    </section>

    <section class="contact">
      <p class="contact-phone">(408)614-2907</p>
      <p class="contact-web">bramblecresthomes.com</p>
    </section>

    <section class="licenses">
      <p>CADRE #02794613</p>
      <p>CONTRACTORS<br>LICENSE #1178524</p>
    </section>
  </main>
</body>
</html>
```